Venture Capital firm needs modern business cards

We are a Venture Capital firm within financial services/Asset management. The industry generally has basic business cards with black, blue and maybe green/yellow design elements.
Our firm has a four-colour swoosh logo. We are based in London and want to stand out, just a little bit!, from the crowd. Our company is called LORV Investments and the 'C' stands for collaboration thus using makerswarm is a natural portal for our business card design competition. Our logo came via makerswarm too!
We use 'Venture Partner in Asset Management' as our tagline and this is Trademark registered. We operate in a conservative industry and we should not overstep our mark. The logo is colorful as it is and therefore the rest of the design should not be too fanciful.
The objective is twofold: make our logo element stick and memorable with our audience, whilst representing a conservative yet young image.
Updates
The Business Card obviously needs a field for Name, Surname, Job Title, Adress fields: Street, City, Postcode, Country, telefone and cell number, website address, etc.
We have uploaded the ai file. We trust that these are OK. If not, please advise.
Reason: We have have been busy with a client engagement. We will set the project as Guaranteed in return for the troubles we cause. Apologies for the confusion.
Thank you all for these great and creative design suggestions. The team is very happy with a number of your ideas! We will be in touch tomorrow to give individual feedback before the project closes on Friday. We look forward to working with some of you to narrow down your creations. Thank you, LORV Investments team.
All,
Target Market(s)
Financial Services Professionals, Investors, Media, 35-70 years, mainly male, well educated
Industry/Entity Type
Conservative
Requirements
Must have
- We must make use of our logo and potential tagline 'Venture Partner in Asset Management' as we are establishing a new Brand and new company in the market.
We can use 'LORV', 'LORV Investments', and 'LORV Investments'+tagline 'Venture Partner in Asset Management' or simply the four-colour swoosh plus the name of the company as part of the text. (see files)
All design elements are available in black or grey-scale if required. (grey scale swoosh attached).
Due to regulation we must have the following wording on the card in small print 'LORV Investments is an Appointed Representative of Bramwell Holdings Partnership Limited, which is authorised by the Monetary Oversight Board'.
Nice to have
- We would consider designs that make use of different printing techniques such embossing/debossing, UV spot etc.
We attach our colour palette in the files section for your reference.
Should not have
- The font we use for our company name is 'EXO' so do not use a font style that clashes with the corporate fonts, please.
Do not use other design elements than the ones we provide in the file library as part of this project.

```html
<!DOCTYPE html>
<html lang="en">
<head>
<meta charset="utf-8">
<title>LORV Investments – Business Card</title>
<link rel="stylesheet" href="https://fonts.googleapis.com/css2?family=Arimo:wght@400;700&family=Roboto+Condensed:wght@700&display=swap">
<style>
  :root {
    --page-bg: #e9e9e9;
    --card-bg: #f7f7f5;
    --ink: #4a4a4a;
    --ink-soft: #7a7a7a;
    --ink-faint: #a8a8a8;
    --accent-green: #8cc63f;
    --divider: #cfcfcf;
  }
  * { box-sizing: border-box; margin: 0; padding: 0; }
  html, body {
    width: 1200px; height: 800px; overflow: hidden;
    background: var(--page-bg);
    font-family: "Arimo", Arial, sans-serif;
    color: var(--ink);
  }
  .sheet {
    position: relative; width: 1200px; height: 800px;
    display: flex; align-items: center; justify-content: center; gap: 60px;
  }
  .card {
    position: relative; width: 520px; height: 300px;
    background: var(--card-bg);
    box-shadow: 0 2px 6px rgba(0,0,0,0.12);
  }
  /* back side */
  .card-back { display: flex; align-items: center; justify-content: center; gap: 18px; }
  .brand-dot { width: 34px; height: 34px; border-radius: 50%; background: var(--accent-green); }
  .brand-large { font-size: 72px; font-weight: 700; color: var(--ink); letter-spacing: 1px; }
  /* front side */
  .card-front { display: flex; }
  .brand-panel {
    width: 48%; display: flex; align-items: center; justify-content: center; gap: 10px;
    border-right: 1px solid var(--divider); margin: 28px 0 48px;
  }
  .brand-panel .brand-dot { width: 18px; height: 18px; }
  .brand-name { font-size: 30px; font-weight: 700; color: var(--ink); }
  .contact-panel {
    flex: 1; display: flex; flex-direction: column; align-items: center;
    padding-top: 30px; text-align: center;
  }
  .person-name {
    font-family: "Roboto Condensed", "Arial Narrow", sans-serif;
    font-weight: 700; font-size: 22px; color: var(--accent-green); letter-spacing: 0.3px;
  }
  .person-role { font-size: 12px; color: var(--ink-soft); margin-bottom: 10px; }
  .contact-icon { width: 14px; height: 14px; margin: 4px 0 3px; fill: var(--ink-faint); }
  .contact-line { font-size: 12.5px; color: var(--ink-soft); line-height: 1.3; }
  .legal-note {
    position: absolute; left: 20px; right: 20px; bottom: 12px;
    font-size: 6.5px; color: var(--ink-faint); text-align: right;
  }
</style>
</head>
<body>
<main class="sheet">
  <section class="card card-back" aria-label="Business card back">
    <span class="brand-dot"></span>
    <span class="brand-large">LORV</span>
  </section>

  <section class="card card-front" aria-label="Business card front">
    <div class="brand-panel">
      <span class="brand-dot"></span>
      <span class="brand-name">LORV Investments</span>
    </div>
    <div class="contact-panel">
      <h1 class="person-name">DANIEL MARLOWE</h1>
      <p class="person-role">Graphic designer</p>

      <svg class="contact-icon" viewBox="0 0 14 14" aria-hidden="true">
        <path d="M3.5 0.5h7a1 1 0 0 1 1 1v11a1 1 0 0 1-1 1h-7a1 1 0 0 1-1-1v-11a1 1 0 0 1 1-1zM4 2v8.5h6V2zM7 11.2a0.8 0.8 0 1 0 0.01 0z" fill-rule="evenodd"/>
      </svg>
      <p class="contact-line">+44 20 7946 0312</p>

      <svg class="contact-icon" viewBox="0 0 14 14" aria-hidden="true">
        <path d="M1 3h12v8H1zM1.6 3.4L7 7.6l5.4-4.2v0.9L7 8.5 1.6 4.3z"/>
      </svg>
      <p class="contact-line">http://www.lorv-invest.net</p>

      <svg class="contact-icon" viewBox="0 0 14 14" aria-hidden="true">
        <path d="M7 0.5a4.3 4.3 0 0 1 4.3 4.3C11.3 8 7 13.5 7 13.5S2.7 8 2.7 4.8A4.3 4.3 0 0 1 7 0.5zM7 3.2a1.6 1.6 0 1 0 0.01 0z" fill-rule="evenodd"/>
      </svg>
      <address class="contact-line" style="font-style:normal">
        48 Aldermoor Lane<br>Kestwick Row<br>London<br>EC2 4PL
      </address>
    </div>
    <p class="legal-note">LORV Investments is an Appointed Representative of Bramwell Holdings Partnership Limited, which is authorised by the Monetary Oversight Board</p>
  </section>
</main>
</body>
</html>
```